Walk Beside The River

Business Card design

Target Market(s)

People who require support in the commnity

Industry/Entity Type

Mental Health Support

Contact Information for Business Card

Mental Health Support Rosalind Tavener walkbesidetheriver@mailcove.com.au 0481 637 092 PO Box 926 Wattlemere QLD 4599

Colors
6B429C
8869AF
B7A5CE
E3DAEB
F3F0F8

Requirements
Must have
• Logo & details listed above
Should not have
• No red or orange

```html
<!DOCTYPE html>
<html lang="en">
<head>
<meta charset="utf-8">
<title>Walk Beside The River – Business Card</title>
<link rel="stylesheet" href="https://fonts.googleapis.com/css2?family=Open+Sans:wght@400;600;800&display=swap">
<style>
  :root {
    --stage: #2b2b2e;
    --card-dark: #222125;
    --purple: #6b429c;
    --purple-mid: #8869af;
    --purple-light: #b7a5ce;
    --lilac: #e3daeb;
    --mist: #f3f0f8;
    --yellow: #f2ea1d;
    --white: #ffffff;
  }
  * { margin: 0; padding: 0; box-sizing: border-box; }
  html, body {
    width: 1200px; height: 780px; overflow: hidden;
    background: var(--stage);
    font-family: "Open Sans", Arial, sans-serif;
  }
  .stage {
    width: 1200px; height: 780px;
    display: flex; align-items: center; justify-content: center; gap: 40px;
  }
  .card {
    position: relative;
    width: 540px; height: 310px;
    overflow: hidden;
    border-top: 3px solid var(--yellow);
    box-shadow: 0 10px 28px rgba(0,0,0,.45);
  }

  /* Front */
  .card-front { background: var(--card-dark); color: var(--white); }
  .brand {
    position: absolute; left: 28px; top: 24px;
    display: flex; align-items: center; gap: 12px;
  }
  .brand-dot {
    width: 62px; height: 62px; border-radius: 50%;
    background: var(--purple);
    flex: none;
  }
  .brand-name {
    font-size: 14px; font-weight: 600; color: var(--white);
    white-space: nowrap; line-height: 1.25;
  }
  .details {
    position: absolute; left: 28px; bottom: 24px;
    font-size: 12.5px; line-height: 1.6;
  }
  .details .service, .details .contact-person { font-size: 13.5px; }
  .contact-list { list-style: none; margin-top: 4px; }
  .contact-list li { display: flex; align-items: center; gap: 8px; }
  .contact-list svg { width: 12px; height: 12px; flex: none; }
  .holder {
    position: absolute; right: 40px; top: 104px;
    text-align: right;
  }
  .holder-name {
    font-size: 30px; font-weight: 800; line-height: 1.1; letter-spacing: .2px;
    white-space: nowrap;
  }
  .holder-name .first { color: var(--yellow); }
  .holder-name .last { color: var(--purple-mid); }
  .holder-title { font-size: 14.5px; margin-top: 2px; }
  .edge-tab {
    position: absolute; right: 0; top: 140px;
    width: 16px; height: 62px; background: var(--yellow);
  }

  /* Back */
  .card-back {
    background: linear-gradient(105deg, var(--purple) 0%, #6f47a3 55%, var(--purple-mid) 85%, var(--purple-light) 100%);
  }
  .back-pattern { position: absolute; inset: 0; }
  .back-brand {
    position: absolute; right: 56px; bottom: 62px;
    display: flex; align-items: center; gap: 10px;
  }
  .back-brand .brand-dot {
    width: 26px; height: 26px; background: var(--yellow);
  }
  .back-brand .brand-name { font-size: 12px; white-space: normal; max-width: 90px; }
</style>
</head>
<body>
<main class="stage">
  <section class="card card-front" aria-label="Business card front">
    <div class="brand">
      <span class="brand-dot"></span>
      <span class="brand-name">Walk Beside The River</span>
    </div>

    <div class="details">
      <p class="service">Mental Health Support</p>
      <p class="contact-person">Rosalind Tavener</p>
      <ul class="contact-list">
        <li>
          <svg viewBox="0 0 24 24" aria-hidden="true"><path fill="#f2ea1d" d="M6.6 10.8a15.1 15.1 0 0 0 6.6 6.6l2.2-2.2c.3-.3.7-.4 1-.2 1.1.4 2.3.6 3.6.6.6 0 1 .4 1 1V20c0 .6-.4 1-1 1A17 17 0 0 1 3 4c0-.6.4-1 1-1h3.5c.6 0 1 .4 1 1 0 1.3.2 2.5.6 3.6.1.3 0 .7-.2 1z"/></svg>
          <span>0481 637 092</span>
        </li>
        <li>
          <svg viewBox="0 0 24 24" aria-hidden="true"><path fill="#f2ea1d" d="M3 5h18v14H3z"/><path d="M3 5l9 7 9-7" fill="none" stroke="#222125" stroke-width="2"/></svg>
          <span>walkbesidetheriver@mailcove.com.au</span>
        </li>
        <li>
          <svg viewBox="0 0 24 24" aria-hidden="true"><path fill="#f2ea1d" d="M12 2a7 7 0 0 0-7 7c0 5.2 7 13 7 13s7-7.8 7-13a7 7 0 0 0-7-7zm0 9.5A2.5 2.5 0 1 1 12 6.5a2.5 2.5 0 0 1 0 5z"/></svg>
          <span>PO Box 926 Wattlemere QLD 4599</span>
        </li>
      </ul>
    </div>

    <div class="holder">
      <h1 class="holder-name"><span class="first">Marta</span> <span class="last">Velenova</span></h1>
      <p class="holder-title">CEO/Director</p>
    </div>
    <span class="edge-tab"></span>
  </section>

  <section class="card card-back" aria-label="Business card back">
    <div class="back-pattern" role="img" aria-label="Repeating star pattern fading to bright sparkles on the right"></div>
    <div class="back-brand">
      <span class="brand-dot"></span>
      <span class="brand-name">Walk Beside The River</span>
    </div>
  </section>
</main>
</body>
</html>
```